Harborlight Realty Letterhead

Harborlight Realty Guan
417 Calle Marbeso Road, Ste B215
Marisol Bay, GU. 96920

Industry/Entity Type

Real Estate

Font styles to use
Serif

Colors

Designer to choose colors to be used in the design.

```html
<!DOCTYPE html>
<html lang="en">
<head>
<meta charset="utf-8">
<title>Harborlight Realty Letterhead</title>
<link href="https://fonts.googleapis.com/css2?family=Montserrat:wght@400;600;700&family=Questrial&family=Open+Sans:wght@600&display=swap" rel="stylesheet">
<style>
  :root {
    --sky: #6cc5ea;
    --ocean: #0793d3;
    --ink: #6d6e71;
    --paper: #ffffff;
    --backdrop: #e4e5e7;
    --placeholder-a: #f3f3f3;
    --placeholder-b: #e6e6e6;
  }
  html, body {
    margin: 0;
    padding: 0;
    width: 1023px;
    height: 1200px;
    overflow: hidden;
    background: var(--backdrop);
  }
  .page {
    position: absolute;
    left: 98px;
    top: 20px;
    width: 827px;
    height: 1160px;
    background: var(--paper);
    box-shadow: 0 4px 14px rgba(0,0,0,0.18);
    overflow: hidden;
    font-family: "Questrial", sans-serif;
    color: var(--ink);
  }
  .brand {
    position: absolute;
    left: 54px;
    top: 124px;
    display: flex;
    align-items: center;
    gap: 10px;
    padding-right: 10px;
    background: var(--paper);
    z-index: 2;
  }
  .brand-mark {
    width: 12px;
    height: 12px;
    border-radius: 50%;
    background: var(--sky);
  }
  .brand-name {
    font-family: "Montserrat", sans-serif;
    font-weight: 400;
    font-size: 28px;
    letter-spacing: 1px;
    color: var(--sky);
    line-height: 1;
  }
  .header-rule {
    position: absolute;
    left: 0;
    right: 0;
    top: 164px;
    height: 1.5px;
    background: var(--sky);
  }
  .sender {
    position: absolute;
    left: 54px;
    top: 251px;
    font-family: "Montserrat", sans-serif;
    font-size: 14.5px;
    line-height: 18px;
  }
  .sender-name {
    margin: 0 0 8px;
    font-weight: 700;
    font-size: 26px;
    line-height: 30px;
    letter-spacing: 0.3px;
    color: var(--sky);
  }
  .sender-line { margin: 0 0 8px; }
  .sender-address { margin: 0; }
  .letter-date {
    position: absolute;
    right: 57px;
    top: 352px;
    margin: 0;
    font-family: "Open Sans", sans-serif;
    font-weight: 600;
    font-size: 16.5px;
    line-height: 22px;
    color: var(--ink);
  }
  .letter-body {
    position: absolute;
    left: 54px;
    top: 409px;
    width: 719px;
    font-size: 15px;
    letter-spacing: 0.15px;
    line-height: 18px;
    text-align: justify;
  }
  .letter-body p { margin: 0; }
  .letter-body .gap { margin-top: 18px; }
  .letter-body .gap-wide { margin-top: 38px; }
  .signoff {
    position: absolute;
    left: 55px;
    top: 810px;
    margin: 0;
    font-size: 17px;
    line-height: 22px;
    color: var(--ink);
  }
  .signature {
    position: absolute;
    left: 57px;
    top: 851px;
    width: 144px;
    height: 91px;
    background: linear-gradient(135deg, var(--placeholder-a), var(--placeholder-b));
  }
  .office {
    position: absolute;
    left: 54px;
    top: 1019px;
    font-family: "Montserrat", sans-serif;
    font-size: 16.5px;
    line-height: 20px;
    color: var(--ink);
  }
  .office-name {
    margin: 0 0 3px;
    font-weight: 600;
    font-size: 19.5px;
    line-height: 24px;
    color: var(--ocean);
  }
  .office p { margin: 0; }
</style>
</head>
<body>
  <main class="page">
    <header>
      <div class="brand">
        <span class="brand-mark"></span>
        <span class="brand-name">Harborlight Realty</span>
      </div>
      <div class="header-rule"></div>
    </header>

    <section class="sender">
      <h1 class="sender-name">MARA QUINTERO</h1>
      <p class="sender-line">0147-820-365</p>
      <p class="sender-line">hello@tidecrestmail.com</p>
      <p class="sender-address">5870 Lantern Cove Ln. Suite<br>214 Austin, TX 0000</p>
    </section>

    <p class="letter-date">12 December, 2023</p>

    <article class="letter-body">
      <p>Lorem ipsum dolor sit amet, consectetuer adipiscing elit, sed diam nonummy nibh euismod tincidunt ut laoreet dolore magna aliquam erat volutpat. Ut wisi enim ad minim veniam, quis nostrud exerci tation ullamcorper suscipit lobortis nisl ut aliquip ex ea commodo consequat. Duis autem vel eum iriure dolor in hendrerit in vulputate velit esse molestie consequat, vel illum dolore eu feugiat nulla facilisis at vero eros et accumsan et iusto odio dignissim qui blandit praesent luptatum zzril delenit augue duis dolore te feugait nulla facilisi.</p>
      <p class="gap">Lorem ipsum dolor sit amet, cons ectetuer adipiscing elit, sed diam nonummy nibh euismod tincidunt ut laoreet dolore magna aliquam erat volutpat. Ut wisi enim ad minim veniam, quis nostrud exerci tation ullamcorper suscipit lobortis nisl ut aliquip ex ea commodo consequat.</p>
      <p>Lorem ipsum dolor sit amet, consectetuer adipiscing elit, sed diam nonummy nibh euismod tincidunt ut laoreet dolore magna aliquam erat</p>
      <p class="gap-wide">Lorem ipsum dolor sit amet, cons ectetuer adipiscing elit, sed diam nonummy nibh euismod tincidunt ut laoreet dolore magna aliquam erat volutpat. Ut wisi enim ad minim veniam, quis nostrud exerci tation ullamcorper suscipit lobortis nisl ut aliquip ex ea commodo consequat. Lorem ipsum dolor sit zamet, consectetuer adipiscing elit, sed diam nonummy nibh euismod tincidunt ut laoreet dolore magna aliquam erat volutpat. Ut wisi enim ad minim veniam, quis nostrud exerci tation ullamcorper suscipit lobortis nisl ut aliquip ex ea commodo consequat. Duis autem vel eum iriure.</p>
    </article>

    <p class="signoff">Managing Director</p>
    <div class="signature" role="img" aria-label="Handwritten signature of the managing director"></div>

    <footer class="office">
      <p class="office-name">Harborlight Realty Guan</p>
      <p>417 Calle Marbeso Road, Ste B215</p>
      <p>Marisol Bay, GU. 96920</p>
    </footer>
  </main>
</body>
</html>
```